Website Design for Employee Moral and Happiness Company

Looking for a clean website design that explains our features in a step by step manner so our visitors know exactly what our site does before logging in.

The site is called "Velrato". See logo design and video for a sample of style and an overview of what we do.

Target Market(s)

Business owners that are looking to retain employees.

Number of Pages Required

1 page

```html
<!DOCTYPE html>
<html lang="en">
<head>
<meta charset="UTF-8">
<title>Velrato — Employee Happiness</title>
<link rel="stylesheet" href="https://fonts.googleapis.com/css2?family=Jost:wght@400;500;600&family=Nunito:wght@400;600;700;800&display=swap">
<style>
  :root {
    --header-bg: #e8dfd6;
    --orange: #ff6600;
    --orange-deep: #e35a06;
    --navy: #2b3d5c;
    --ink: #2d2d2d;
    --white: #ffffff;
    --muted: #b9c1cd;
    --divider: #52637f;
  }
  * { margin: 0; padding: 0; box-sizing: border-box; }
  html, body { width: 1200px; height: 698px; overflow: hidden; }
  body { font-family: "Nunito", sans-serif; position: relative; background: var(--white); }
  a { text-decoration: none; color: inherit; }

  .site-header { position: absolute; left: 0; top: 0; width: 1200px; height: 90px; background: var(--header-bg); }
  .brand { position: absolute; left: 66px; top: 18px; display: flex; align-items: center; gap: 8px;
    font-family: "Jost", sans-serif; font-weight: 600; font-size: 38px; color: #111; line-height: 1; }
  .brand-dot { width: 12px; height: 12px; border-radius: 50%; background: var(--orange); }
  .main-nav a, .footer-nav a { position: absolute; white-space: nowrap; }
  .main-nav a { top: 34px; font-size: 15.5px; color: var(--ink); }
  .main-nav a.is-active { color: var(--orange); text-decoration: underline; text-underline-offset: 3px; }
  .login { position: absolute; display: flex; align-items: center; gap: 8px; font-size: 15.5px; }
  .login svg { width: 12px; height: 12px; }
  .header-login { left: 907px; top: 34px; color: var(--ink); }
  .btn-signup { position: absolute; width: 140px; height: 45px; border-radius: 23px; background: var(--orange);
    color: var(--white); font-weight: 800; font-size: 16px; display: flex; align-items: center; justify-content: center; }
  .header-signup { left: 995px; top: 18px; }

  .hero { position: absolute; left: 0; top: 90px; width: 1200px; height: 414px; background: var(--orange); overflow: hidden; }
  .hero-shapes { position: absolute; inset: 0; }
  .hero-title { position: absolute; left: 0; width: 1200px; top: 88px; text-align: center;
    font-family: "Jost", sans-serif; font-weight: 500; font-size: 26px; color: var(--white); letter-spacing: 0.3px; }
  .hero-title .stat { color: var(--navy); }
  .hero-text { position: absolute; left: 240px; width: 720px; top: 136px; text-align: center;
    font-size: 17px; line-height: 30px; color: var(--white); }
  .btn-outline { position: absolute; left: 478px; top: 268px; width: 245px; height: 52px; border: 2px solid var(--white);
    border-radius: 27px; color: var(--white); font-weight: 800; font-size: 16px; display: flex; align-items: center; justify-content: center; word-spacing: 3px; }
  .step-label { position: absolute; left: 1113px; top: 321px; font-size: 12px; font-weight: 600; color: var(--white); }

  .site-footer { position: absolute; left: 0; top: 504px; width: 1200px; height: 194px; background: var(--navy); color: var(--white); }
  .footer-nav a { top: 42px; font-size: 15.5px; font-weight: 700; }
  .footer-login { left: 906px; top: 42px; font-weight: 700; }
  .footer-signup { left: 994px; top: 26px; }
  .footer-divider { position: absolute; left: 37px; top: 134px; width: 1125px; height: 1px; background: var(--divider); }
  .copyright { position: absolute; left: 67px; top: 153px; font-size: 15.5px; color: var(--muted); }
  .legal { position: absolute; right: 66px; top: 153px; font-size: 15.5px; color: var(--muted); }
  .legal a { text-decoration: underline; text-underline-offset: 3px; }
</style>
</head>
<body>
  <header class="site-header">
    <div class="brand"><span>Velrato</span><span class="brand-dot"></span></div>
    <nav class="main-nav">
      <a class="is-active" style="left:278px">Home</a>
      <a style="left:342px">Boring Work Events</a>
      <a style="left:499px">Introducing Velrato</a>
      <a style="left:654px">Why Velrato</a>
      <a style="left:767px">Testimonials</a>
    </nav>
    <a class="login header-login">
      <svg viewBox="0 0 12 12" fill="none" stroke="currentColor" stroke-width="1.2"><path d="M7 1h4v10H7M1 6h6M5 4l2 2-2 2"/></svg>
      Login
    </a>
    <a class="btn-signup header-signup">SIGN UP</a>
  </header>

  <section class="hero">
    <svg class="hero-shapes" width="1200" height="414" viewBox="0 0 1200 414">
      <path d="M0 0 H505 C430 40 400 60 360 100 C310 150 230 160 160 200 C90 240 40 290 0 240 Z" fill="var(--orange-deep)" opacity="0.75"/>
      <path d="M980 414 C1030 380 1090 360 1140 340 C1170 330 1190 320 1200 316 V414 Z" fill="var(--orange-deep)" opacity="0.85"/>
      <rect role="img" aria-label="Dot grid decoration" x="165" y="36" width="135" height="164" fill="#b34a10" opacity="0.12"/>
      <rect role="img" aria-label="Dot grid decoration" x="948" y="338" width="135" height="76" fill="#b34a10" opacity="0.12"/>
      <g class="step-track" stroke="var(--white)" stroke-width="1.5" fill="var(--orange)">
        <line x1="1174" y1="81" x2="1174" y2="329"/>
        <circle cx="1174" cy="81" r="5.6"/>
        <circle cx="1174" cy="122" r="5.6"/>
        <circle cx="1174" cy="163" r="5.6"/>
        <circle cx="1174" cy="204" r="5.6"/>
        <circle cx="1174" cy="246" r="5.6"/>
        <circle cx="1174" cy="287" r="5.6"/>
        <circle cx="1174" cy="329" r="10.5" fill="#f3b185" stroke="none"/>
        <circle cx="1174" cy="329" r="6" fill="var(--white)" stroke="none"/>
      </g>
    </svg>
    <h1 class="hero-title">velrato is trusted by over <span class="stat">2000+</span> business owners</h1>
    <p class="hero-text">Lorem ipsum dolor sit amet, consectetur adipiscing elit, sed do eiusmod tempor incididunt ut labore et dolore magna aliqua. Quis ipsum suspendisse ultrices gravida. Risus commodo viverra maecenas accumsan lacus vel facilisis.</p>
    <a class="btn-outline">SIGN UP NOW</a>
    <span class="step-label">Sign up</span>
  </section>

  <footer class="site-footer">
    <nav class="footer-nav">
      <a style="left:67px">Home</a>
      <a style="left:128px">Boring Work Events</a>
      <a style="left:284px">Introducing Velrato</a>
      <a style="left:438px">Why Velrato</a>
      <a style="left:548px">Testimonials</a>
    </nav>
    <a class="login footer-login">
      <svg viewBox="0 0 12 12" fill="none" stroke="currentColor" stroke-width="1.2"><path d="M7 1h4v10H7M1 6h6M5 4l2 2-2 2"/></svg>
      Login
    </a>
    <a class="btn-signup footer-signup">SIGN UP</a>
    <div class="footer-divider"></div>
    <p class="copyright">Copyright© 2022 Velrato. All rights reserved.</p>
    <p class="legal"><a>Privacy Policy</a> | <a>Terms Of Service</a></p>
  </footer>
</body>
</html>
```